Long webpage to explain and sell a complex concept

Accountancy firm wishes to explain Management Accounting to a Small Business audience. We have written the text, assembled a couple of charts and quotes and some concept photos.
There is a lot of text and it is required to explain this type of accounting.
Rather than have a long single block of text which is less likely to be read, we want to break it up with pictures, appropriate white space, diagrams etc. Someone landing on this page will then scroll down reading the text which is designed to keep you reading more.
The page on the website where this will go is https://www.brindlequay.com.au/services/management-accountants-perth/
So the fonts/colours need to fit in. Notice there is a pallet of colours which can be seen here: https://www.brindlequay.com.au/services/

Target Market(s)

Small Business owners in Perth, Western Australia

Number of Pages Required

1 page

Requirements
Must have
• The look and feel needs to match the website indicated in the description above. However we're happy to make the design of this page more interesting than the rest of the site.

```html
<!DOCTYPE html>
<html lang="en">
<head>
<meta charset="utf-8">
<title>Management Accounting – Understanding Profit</title>
<link href="https://fonts.googleapis.com/css2?family=Open+Sans:ital,wght@0,300;0,400;1,400&family=Lora:ital,wght@0,400;0,600;1,400&display=swap" rel="stylesheet">
<style>
  :root {
    --ink: #3a3a3a;
    --ink-strong: #1f1f1f;
    --plum: #6e1470;
    --olive: #6f6a12;
    --rule: #8a8a8a;
    --chart-frame: #e6e0e6;
    --grid: #e4e4e4;
    --axis-text: #777777;
    --income: #1aaee8;
    --expense: #8ccf4d;
    --profit: #e8161b;
    --paper: #ffffff;
  }
  * { margin: 0; padding: 0; box-sizing: border-box; }
  html, body { width: 1200px; height: 2732px; overflow: hidden; background: var(--paper); }
  body { position: relative; font-family: "Lora", Georgia, serif; color: var(--ink); font-size: 17.5px; line-height: 38px; letter-spacing: -0.1px; }

  .heading-block { position: absolute; }
  .heading-block h2 { font-family: "Open Sans", Arial, sans-serif; font-weight: 300; font-size: 49px; line-height: 71px; white-space: nowrap; letter-spacing: -0.5px; }
  .heading-profit { left: 604px; top: 76px; height: 264px; border-left: 1px solid var(--rule); padding: 18px 0 0 54px; }
  .heading-profit h2 { color: var(--plum); }
  .heading-ups { left: 120px; top: 1181px; width: 459px; height: 224px; border-right: 1px solid var(--olive); padding: 12px 56px 0 0; text-align: right; }
  .heading-ups h2 { color: var(--olive); }

  .concept-photo { position: absolute; left: 22px; top: 374px; width: 480px; height: 382px;
    background: radial-gradient(ellipse at 45% 55%, #6f8a3c 0%, #a7b56a 30%, #e9e2c8 58%, #ffffff 78%); }

  .intro { position: absolute; left: 192px; top: 395px; width: 800px; }
  .intro .float-gap { float: left; width: 413px; height: 380px; }
  .intro p { text-align: justify; margin-bottom: 22px; }

  .ups-text { position: absolute; left: 190px; top: 1452px; width: 388px; text-align: justify; }
  .chart { position: absolute; left: 605px; top: 1460px; width: 548px; height: 352px; border: 3px solid var(--chart-frame); }
  .chart-caption { position: absolute; left: 645px; top: 1838px; width: 470px; font-family: "Open Sans", Arial, sans-serif; font-style: italic; font-size: 13px; line-height: 21px; letter-spacing: 0; color: var(--ink); }

  .body-text { position: absolute; left: 194px; top: 2008px; width: 796px; }
  .body-text p { text-align: justify; margin-bottom: 26px; }
  .body-text strong { font-weight: 600; color: var(--ink-strong); }
  .causes { list-style: none; margin: 0 0 24px 74px; width: 440px; }
  .causes li { position: relative; padding-left: 26px; }
  .causes li::before { content: ""; position: absolute; left: 0; top: 17px; width: 5px; height: 5px; border-radius: 50%; background: var(--ink); }
</style>
</head>
<body>

<header class="heading-block heading-profit">
  <h2>"Profit" isn't<br>what you might<br>think it is</h2>
</header>

<div class="concept-photo" role="img" aria-label="Concept photo: a young plant growing from a pile of coins beside a measuring tape"></div>

<section class="intro">
  <div class="float-gap"></div>
  <p>Even when the P&amp;L profit is calculated correctly, the profit it shows is accounting profit and may not align with many business owner's idea or expectations of profit. We need to understand what it means. Buying stock, assets/plant and paying down debt (such as HP loans) will all drain cash but not create a blip on the P&amp;L profit. Plant which you bought years ago but is no longer supporting the business still being depreciated might be correct accounting, but giving you a mis-leading profit figure.</p>
  <p>The average P&amp;L printed off without any checking/updating will be way off to the point of being misleading.</p>
  <p>OK, so you P&amp;L tells you what you earned in the past month (or year-to-date, or year etc). This is much more useful than just looking at the bank account transactions, but it still doesn't forecast into the near future to give you time to avoid the proverbial rocks.</p>
</section>

<header class="heading-block heading-ups">
  <h2>The<br>Ups and Downs<br>of Profit</h2>
</header>

<p class="ups-text">And the problems don't end there. Even in the very best businesses with the most stable trading conditions, the profit figure from month to month bounces up and down like kangaroo in a coffee shop. As you know, Profit is what you have left over when expenses are subtracted from income. Now both income and expenses vary from month to month, and they are generally much larger than the difference between them (the profit). So when you subtract one from the other, any 'noise' in those expenses and that income get magnified enormously.<br>Now you could</p>

<figure class="chart">
  <svg width="542" height="346" viewBox="0 0 542 346" font-family="Open Sans, Arial, sans-serif">
    <text x="271" y="22" text-anchor="middle" font-size="14" fill="#666">Forecast</text>
    <g stroke="var(--grid)" stroke-width="1">
      <line x1="55" y1="45" x2="530" y2="45"/><line x1="55" y1="82.5" x2="530" y2="82.5"/>
      <line x1="55" y1="120" x2="530" y2="120"/><line x1="55" y1="157.5" x2="530" y2="157.5"/>
      <line x1="55" y1="195" x2="530" y2="195"/><line x1="55" y1="232.5" x2="530" y2="232.5"/>
      <line x1="55" y1="270" x2="530" y2="270"/><line x1="55" y1="307.5" x2="530" y2="307.5"/>
    </g>
    <g font-size="9" fill="var(--axis-text)" text-anchor="end">
      <text x="44" y="48">300,000</text><text x="44" y="85.5">250,000</text>
      <text x="44" y="123">200,000</text><text x="44" y="160.5">150,000</text>
      <text x="44" y="198">100,000</text><text x="44" y="235.5">50,000</text>
      <text x="44" y="273">0</text><text x="44" y="310.5">-50,000</text>
    </g>
    <g font-size="9" fill="var(--axis-text)" text-anchor="middle">
      <text x="75" y="286">Jul 19</text><text x="115" y="286">Aug 19</text><text x="155" y="286">Sep 19</text>
      <text x="195" y="286">Oct 19</text><text x="235" y="286">Nov 19</text><text x="275" y="286">Dec 19</text>
      <text x="315" y="286">Jan 20</text><text x="355" y="286">Feb 20</text><text x="395" y="286">Mar 20</text>
      <text x="435" y="286">Apr 20</text><text x="475" y="286">May 20</text><text x="515" y="286">Jun 20</text>
    </g>
    <g fill="none" stroke-width="2.5" stroke-linejoin="round">
      <polyline stroke="var(--expense)" points="75,163.5 115,159.75 155,159.75 195,159.75 235,136.5 275,159.75 315,159.75 355,159.75 395,159.75 435,159.75 475,136.5 515,159.75"/>
      <polyline stroke="var(--income)" points="75,161.25 115,148.5 155,111 195,165 235,129.75 275,130.5 315,114 355,121.5 395,113.25 435,131.25 475,133.5 515,86.25"/>
      <polyline stroke="var(--profit)" points="75,267.75 115,258 155,221.25 195,275.25 235,264 275,240.75 315,223.5 355,231 395,222.75 435,241.5 475,267 515,196.5"/>
    </g>
    <g font-size="9" fill="var(--axis-text)">
      <line x1="160" y1="330" x2="185" y2="330" stroke="var(--income)" stroke-width="2.5"/><text x="187" y="333">Income</text>
      <line x1="230" y1="330" x2="255" y2="330" stroke="var(--expense)" stroke-width="2.5"/><text x="257" y="333">All Expenses</text>
      <line x1="320" y1="330" x2="345" y2="330" stroke="var(--profit)" stroke-width="2.5"/><text x="347" y="333">Net Profit</text>
    </g>
  </svg>
</figure>

<p class="chart-caption">[This is a budget forecast from a client for the 19/20 financial year. Despite predicting smooth sailing and a healthy profit of $445,000, notice that in some months, their projected profit was very low or even negative.]</p>

<section class="body-text">
  <p>Take a look at this budget from an actual company for the FY20 year. This is a plan for an ideal (but realistic) outcome. Notice that the business will be in losses in October, and very low profit in July and May - <strong>and that's if everything goes well!</strong></p>
  <p>Just imagine reading your P&amp;L in October. After applying the defibrillator, you start the task of working out why you made a loss - is there something serious wrong? - are we solvent? - what does this mean for our future profitability?</p>
  <p>Well here’s the thing, it might not mean trouble. We have clients with very profitable businesses who, due simply to timing, have some months in losses. And we don't just mean cash losses due to GST etc - we mean their P&amp;L shows a loss. Common causes often include:</p>
  <ul class="causes">
    <li>Three fortnightly pay periods occurring in a<br>calendar months</li>
    <li>Large annual insurance bills</li>
    <li>Income for services billed every quarter rather</li>
  </ul>
  <p>So what's the answer?</p>
</section>

</body>
</html>
```